To design a brand identity that is simple and creative with 'Corvane' as the brand name, I like modern simple fonts like helvetica neue, I want to print both sides of the card, I am open to dark front and white back, but the design needs to transfer well to letter heads and email signatures, I am looking for sophisticated and elegant, but open minded about clever and off the wall, I do not do 'boring' Corvane Ventures is the mother company for a small group, specialising in Management & consulting, Software development and construction, we have a high level of integrity, we are transparent and accountable for what we do. my images are provided as a guide only, Im not expecting them to be just copied, Im looking for a creator and passionate thinker, who will put life into their work.

Target Market(s)

usually business minded people who are looking for something different in me, such as leadership, confidence and focus with thinking that is per haps a little outside the box..

Industry/Entity Type

Construction

Requirements
Must have
• clean, minmalistic
Nice to have
• custom logo
Should not have
• boring, traditional

```html
<!DOCTYPE html>
<html lang="en">
<head>
<meta charset="utf-8">
<title>Corvane Business Card</title>
<link rel="stylesheet" href="https://fonts.googleapis.com/css2?family=Open+Sans:wght@400;600;700&display=swap">
<style>
  :root {
    --canvas-bg: #e9e7e4;
    --card-dark: #0e0e0f;
    --card-dark-edge: #1c1c1e;
    --card-light: #ffffff;
    --brand-orange: #e8643a;
    --brand-gold: #f3b21c;
    --text-white: #f2f2f2;
    --text-grey: #4a4a4a;
    --text-soft: #8a8a8a;
  }
  * { margin: 0; padding: 0; box-sizing: border-box; }
  html, body {
    width: 1200px;
    height: 720px;
    overflow: hidden;
    background: var(--canvas-bg);
    font-family: "Open Sans", Arial, sans-serif;
  }
  .canvas {
    position: relative;
    width: 1200px;
    height: 720px;
  }
  .card {
    position: absolute;
    width: 540px;
    height: 309px;
    border-radius: 4px;
    box-shadow: 0 6px 18px rgba(0,0,0,0.18);
    overflow: hidden;
  }

  /* Front: dark side */
  .card--front {
    left: 40px;
    top: 205px;
    background:
      repeating-linear-gradient(90deg, rgba(255,255,255,0.015) 0 1px, transparent 1px 3px),
      linear-gradient(160deg, var(--card-dark-edge), var(--card-dark) 60%);
  }
  .card--front .brand-name {
    position: absolute;
    left: 32px;
    top: 56px;
    font-size: 58px;
    font-weight: 600;
    line-height: 1;
    color: var(--brand-orange);
  }
  .card--front .brand-dot {
    position: absolute;
    left: 390px;
    top: 40px;
    width: 118px;
    height: 118px;
    border-radius: 50%;
    background: var(--brand-gold);
  }
  .contact {
    position: absolute;
    left: 32px;
    top: 182px;
    color: var(--text-white);
  }
  .contact__name {
    font-size: 16px;
    font-weight: 700;
    color: var(--brand-orange);
    line-height: 1.2;
  }
  .contact__title {
    font-size: 13px;
    font-weight: 400;
    margin-bottom: 8px;
  }
  .contact__line {
    display: flex;
    align-items: center;
    gap: 6px;
    font-size: 12.5px;
    line-height: 1.7;
  }
  .contact__line svg { width: 11px; height: 11px; flex: none; }
  .contact__line--address { margin-top: 6px; }

  /* Back: light side */
  .card--back {
    left: 620px;
    top: 205px;
    background: var(--card-light);
  }
  .card--back .brand-dot {
    position: absolute;
    left: 34px;
    top: 92px;
    width: 96px;
    height: 96px;
    border-radius: 50%;
    background: var(--brand-gold);
  }
  .card--back .brand-name {
    position: absolute;
    left: 152px;
    top: 94px;
    font-size: 62px;
    font-weight: 600;
    line-height: 1;
    color: var(--brand-orange);
  }
  .tagline {
    position: absolute;
    left: 156px;
    top: 166px;
    font-size: 15px;
    font-weight: 400;
    letter-spacing: 0.3px;
    color: var(--text-soft);
  }
  .divisions {
    position: absolute;
    left: 0;
    right: 0;
    bottom: 34px;
    text-align: center;
    font-size: 19px;
    font-weight: 400;
    color: var(--text-grey);
    letter-spacing: 0.2px;
  }
</style>
</head>
<body>
<main class="canvas">

  <section class="card card--front" aria-label="Card front">
    <div class="brand-name">Corvane</div>
    <div class="brand-dot" aria-hidden="true"></div>

    <div class="contact">
      <div class="contact__name">Your Name</div>
      <div class="contact__title">Title</div>
      <div class="contact__line">
        <svg viewBox="0 0 12 12" aria-hidden="true">
          <circle cx="6" cy="6" r="5.3" fill="none" stroke="var(--brand-orange)" stroke-width="1.2"/>
          <path d="M4.2 3.4c.4 2.3 1.6 3.8 3.6 4.8l.6-.9-1-.6-.5.5C6 6.7 5.4 6 5.1 5l.5-.5-.5-1z" fill="var(--brand-orange)"/>
        </svg>
        <span>+61 0400 582 913</span>
      </div>
      <div class="contact__line">
        <svg viewBox="0 0 12 12" aria-hidden="true">
          <rect x="1" y="2.5" width="10" height="7" rx="1" fill="var(--brand-orange)"/>
          <path d="M1.5 3.2 6 6.6l4.5-3.4" fill="none" stroke="var(--card-dark)" stroke-width="0.9"/>
        </svg>
        <span>names@corvane.ventures</span>
      </div>
      <div class="contact__line contact__line--address">PO Box 418 Perth 6031</div>
    </div>
  </section>

  <section class="card card--back" aria-label="Card back">
    <div class="brand-dot" aria-hidden="true"></div>
    <div class="brand-name">Corvane</div>
    <div class="tagline">building what comes next</div>
    <div class="divisions">Management &bull; Software &bull; Construction</div>
  </section>

</main>
</body>
</html>
```